Bork Ventures, Inc. Website redesign

Revamp the website, it is old and outdated. www.borkventuresinc.example

Target Market(s)

Information Technology Consulting and Staffing

Coding

Coded - Design and coding required

Number of Pages Required

5+ page

Colors

Designer to choose colors to be used in the design.

Requirements
Must have
• Outlined text boxes just like from the Tolvane.example site. A clean look

```html
<!DOCTYPE html>
<html lang="en">
<head>
<meta charset="utf-8">
<title>Bork Ventures, Inc.</title>
<link href="https://fonts.googleapis.com/css2?family=Raleway:wght@400;500;600;700&family=Roboto:wght@400;500;700&display=swap" rel="stylesheet">
<style>
:root{
  --red:#a11a31;
  --red-dark:#7e1024;
  --ink:#1f1f22;
  --text:#333336;
  --muted:#6a6a70;
  --line:#d9d9dc;
  --navy:#151b2c;
  --footer:#3a3a3d;
  --white:#ffffff;
}
*{margin:0;padding:0;box-sizing:border-box}
html,body{width:1200px;height:4470px;overflow:hidden;background:var(--white)}
body{position:relative;font-family:'Roboto',sans-serif;color:var(--text)}
.abs{position:absolute}
.heading{font-family:'Raleway',sans-serif;font-weight:400;color:var(--ink);text-align:center;font-size:36px}
.heading b{color:var(--red);font-weight:700}
.btn{position:absolute;display:flex;align-items:center;justify-content:center;gap:10px;border-radius:28px;font-family:'Roboto',sans-serif;font-weight:700;font-size:16px;text-decoration:none}
.btn-solid{background:var(--red);color:var(--white)}
.btn-outline{border:2px solid var(--red);color:var(--red);background:var(--white)}
.btn .arrow{width:16px;height:16px}

/* header */
.brand{left:140px;top:8px;display:flex;align-items:center;gap:12px}
.brand-name{font-family:'Raleway',sans-serif;font-weight:700;font-size:38px;color:var(--ink);letter-spacing:1px}
.brand-mark{width:28px;height:28px;background:var(--red)}
.tagline{left:107px;top:70px;font-family:'Raleway',sans-serif;font-variant:small-caps;font-size:28px;color:var(--muted);letter-spacing:.5px}
.header-info{top:18px;display:flex;align-items:center;gap:10px}
.header-info .label{font-size:16px;color:var(--ink);line-height:22px}
.header-info .value{font-size:17px;color:var(--red);font-weight:700}
.nav{right:90px;top:82px;display:flex;gap:30px;font-size:16px;color:var(--text)}
.nav .active{color:var(--red)}

/* hero */
.hero-title{left:87px;top:270px;font-family:'Raleway',sans-serif;font-weight:700;font-size:46px;color:var(--white)}
.hero-text{left:90px;top:333px;width:540px;font-size:17px;line-height:35px;color:var(--white)}

/* welcome */
.welcome-sub{left:0;width:1200px;top:888px;text-align:center;font-weight:500;font-size:20px;color:var(--ink)}
.welcome-text{left:100px;width:1000px;top:926px;text-align:center;font-size:15.5px;line-height:36px;color:var(--text)}
.divider{left:90px;top:1139px;width:1020px;height:1px;background:var(--line)}

/* about */
.about-title{left:600px;top:1228px;font-family:'Raleway',sans-serif;font-size:36px;color:var(--ink)}
.about-title b{color:var(--red);font-weight:700}
.about-text{left:600px;width:510px;top:1282px;font-size:15.5px;line-height:36px;text-align:justify}
.about-text p+p{margin-top:36px}

/* news */
.news-card{position:absolute;top:2953px;width:328px;height:364px;border:1px solid var(--line);background:var(--white)}
.news-photo{height:196px;border-top:3px solid var(--red)}
.news-date{position:absolute;left:16px;top:182px;background:var(--red);color:var(--white);font-size:14px;padding:4px 12px}
.news-title{margin:30px 14px 0;font-size:19px;color:var(--red)}
.news-text{margin:10px 14px 0;font-size:12px;line-height:24px;color:var(--text);text-align:justify}
.news-more{margin:4px 14px 0;font-size:13px;font-weight:700;color:var(--red)}

/* contact */
.contact-sub{left:0;width:1200px;top:3432px;text-align:center;font-size:17px;color:var(--ink)}
.contact-item{top:3481px;width:300px;display:flex;flex-direction:column;align-items:center;text-align:center;font-size:17px;line-height:30px;color:var(--ink)}
.contact-icon{width:84px;height:84px;border-radius:50%;background:var(--red);display:flex;align-items:center;justify-content:center;margin-bottom:16px}
.field{position:absolute;width:431px;height:44px;border:1px solid #e3e3e6;box-shadow:inset 0 2px 0 #f0f0f2;font-size:12px;color:var(--muted);padding:14px 16px}
.field-message{height:149px}

/* footer */
.footer-brand{left:0;width:1200px;top:4188px;display:flex;justify-content:center;align-items:center;gap:40px}
.footer-brand .brand-name{color:var(--white)}
.footer-brand .tagline-text{font-family:'Raleway',sans-serif;font-variant:small-caps;font-size:32px;color:#c9c9cc}
.social{left:0;width:1200px;top:4277px;display:flex;justify-content:center;gap:5px}
.social span{width:32px;height:32px;border:2px solid var(--white);border-radius:50%}
.footer-nav{left:0;width:1200px;text-align:center;font-size:17px;color:var(--white)}
.footer-nav span{margin:0 10px}
</style>
</head>
<body>

<!-- header -->
<div class="abs brand"><span class="brand-name">Bork Ventures</span><span class="brand-mark"></span></div>
<div class="abs tagline">Insight Trust Delivery</div>

<div class="abs header-info" style="left:685px">
  <svg width="40" height="40" viewBox="0 0 40 40"><circle cx="20" cy="20" r="18" fill="none" stroke="var(--red)" stroke-width="2.5"/><path d="M13 12c2-2 3-1 4 1l1 2c0 1-1 2-2 3 1 3 3 5 6 6 1-1 2-2 3-2l2 1c2 1 3 2 1 4-2 2-5 2-9-1-4-3-7-7-7-10 0-2 0-3 1-4z" fill="var(--red)"/></svg>
  <div><div class="label">Call us:</div><div class="value">1-800-555-0142</div></div>
</div>
<div class="abs header-info" style="left:898px">
  <svg width="44" height="44" viewBox="0 0 44 44"><circle cx="18" cy="18" r="14" fill="none" stroke="var(--red)" stroke-width="2.5"/><circle cx="18" cy="18" r="9" fill="none" stroke="var(--red)" stroke-width="1.5"/><path d="M28 28l12 12" stroke="var(--red)" stroke-width="5" stroke-linecap="round"/></svg>
  <div><div class="label">Search:</div><div class="value">Enter search here...</div></div>
</div>
<nav class="abs nav"><span class="active">Home</span><span>About Us</span><span>Our Services</span><span>Strategy</span><span>IT News</span><span>Contact Us</span></nav>

<!-- hero -->
<svg class="abs" style="left:0;top:113px" width="1200" height="660" viewBox="0 0 1200 660" role="img" aria-label="Photo of a glowing red server room with data charts">
  <defs>
    <linearGradient id="heroFill" x1="0" y1="0" x2="1" y2="0.3">
      <stop offset="0" stop-color="#2a0a12"/>
      <stop offset="0.45" stop-color="#6b1226"/>
      <stop offset="0.75" stop-color="#c23355"/>
      <stop offset="1" stop-color="#4a0c1a"/>
    </linearGradient>
  </defs>
  <polygon points="0,0 1200,0 1200,529 867,567 600,633 333,563 0,529" fill="url(#heroFill)"/>
  <polyline points="0,529 127,540 333,563 600,633 867,567 1200,529" fill="none" stroke="var(--red)" stroke-width="3"/>
  <g fill="var(--white)" stroke="var(--red)" stroke-width="3">
    <circle cx="127" cy="540" r="6"/><circle cx="333" cy="563" r="11"/><circle cx="600" cy="633" r="14"/><circle cx="867" cy="567" r="11"/><circle cx="1073" cy="546" r="6"/>
  </g>
</svg>
<h1 class="abs hero-title">Bork Ventures Inc</h1>
<p class="abs hero-text">Lorem ipsum dolor sit amet, consectetur adipiscing elit, sed do eiusmod tempor incididunt ut labore et dolore magna aliqua.</p>
<a class="btn btn-solid" style="left:90px;top:418px;width:207px;height:54px">Read More <svg class="arrow" viewBox="0 0 16 16"><circle cx="8" cy="8" r="8" fill="var(--white)"/><path d="M5 8h6M8 5l3 3-3 3" stroke="var(--red)" stroke-width="2" fill="none"/></svg></a>

<!-- welcome -->
<h2 class="abs heading" style="left:0;width:1200px;top:826px">Welcome to <b>Bork Ventures INC</b></h2>
<div class="abs welcome-sub">Bringing Thought Leadership and Quality to Every Project</div>
<p class="abs welcome-text">Bork Ventures, Inc. is an 8(a) full-service IT consulting company based in the Washington, DC Metro area. We offer specialized, highly customized technology solutions for our customers located throughout the United States.</p>
<a class="btn btn-solid" style="left:385px;top:1015px;width:206px;height:55px">Read More <svg class="arrow" viewBox="0 0 16 16"><circle cx="8" cy="8" r="8" fill="var(--white)"/><path d="M5 8h6M8 5l3 3-3 3" stroke="var(--red)" stroke-width="2" fill="none"/></svg></a>
<a class="btn btn-outline" style="left:609px;top:1015px;width:206px;height:55px">Contact Us <svg class="arrow" viewBox="0 0 16 16"><circle cx="8" cy="8" r="8" fill="var(--red)"/><path d="M5 8h6M8 5l3 3-3 3" stroke="var(--white)" stroke-width="2" fill="none"/></svg></a>
<div class="abs divider"></div>

<!-- about -->
<svg class="abs" style="left:120px;top:1205px" width="450" height="500" viewBox="0 0 450 500">
  <defs>
    <linearGradient id="aboutFill" x1="0" y1="0" x2="1" y2="1">
      <stop offset="0" stop-color="#0e1a3a"/><stop offset="0.5" stop-color="#1f4f9a"/><stop offset="1" stop-color="#071028"/>
    </linearGradient>
  </defs>
  <polygon points="223,3 435,126 435,372 223,495 11,372 11,126" fill="var(--white)" stroke="var(--red)" stroke-width="2.5"/>
  <polygon points="223,20 420,134 420,364 223,478 26,364 26,134" fill="url(#aboutFill)" role="img" aria-label="Photo of a data center aisle with code overlay"/>
</svg>
<h2 class="abs about-title">About <b>Stratavant</b></h2>
<div class="abs about-text">
  <p>Bork Ventures, Inc. is an 8(a) innovative and rapidly growing full-service IT consulting firm. We provide our clients with cutting-edge technologies and the know-how to apply them to their individual business models.</p>
  <p>For over 20 + years, we have been providing reliable IT solutions to businesses in the Washington, DC Metro area and beyond. Our comprehensive services provide clients with unique technology solutions that are customized to meet the specific demands of their business.</p>
</div>
<a class="btn btn-solid" style="left:600px;top:1621px;width:180px;height:48px">Read More <svg class="arrow" viewBox="0 0 16 16"><circle cx="8" cy="8" r="8" fill="var(--white)"/><path d="M5 8h6M8 5l3 3-3 3" stroke="var(--red)" stroke-width="2" fill="none"/></svg></a>

<!-- services -->
<svg class="abs" style="left:0;top:1765px" width="1200" height="1070" viewBox="0 0 1200 1070">
  <defs>
    <radialGradient id="servFill" cx="0.5" cy="0.5" r="0.7">
      <stop offset="0" stop-color="#243049"/><stop offset="1" stop-color="#0d1222"/>
    </radialGradient>
    <linearGradient id="hexPhoto" x1="0" y1="0" x2="1" y2="1">
      <stop offset="0" stop-color="#8a8d96"/><stop offset="0.5" stop-color="#4e5360"/><stop offset="1" stop-color="#2a2e38"/>
    </linearGradient>
  </defs>
  <polygon points="0,4 600,111 1200,4 1200,966 867,985 600,1061 333,985 0,966" fill="url(#servFill)"/>
  <polyline points="0,4 600,111 1200,4" fill="none" stroke="var(--red)" stroke-width="3"/>
  <polyline points="0,966 333,985 600,1061 867,985 1200,966" fill="none" stroke="var(--red)" stroke-width="3"/>
  <g stroke="var(--red)" stroke-width="3" fill="url(#hexPhoto)">
    <polygon points="277,249 433,339 433,519 277,609 121,519 121,339" role="img" aria-label="Photo of a person drawing a network diagram"/>
    <polygon points="600,249 756,339 756,519 600,609 444,519 444,339" role="img" aria-label="Photo of rack-mounted network equipment"/>
    <polygon points="922,249 1078,339 1078,519 922,609 766,519 766,339" role="img" aria-label="Photo of two technicians in a server room"/>
    <polygon points="439,521 595,611 595,791 439,881 283,791 283,611" role="img" aria-label="Photo of an engineer checking server cabinets"/>
    <polygon points="761,521 917,611 917,791 761,881 605,791 605,611" role="img" aria-label="Photo of hands reviewing documents at a desk"/>
  </g>
  <g fill="var(--white)" font-family="Raleway, sans-serif" font-weight="600" font-size="21" text-anchor="middle">
    <text x="277" y="420">Hardware / Software</text><text x="277" y="456">Sales</text>
    <text x="600" y="438">Bork Ventures INC</text>
    <text x="922" y="438">Professional Services</text>
    <text x="439" y="709">Technology Assessment</text>
    <text x="761" y="709">Technology Consulting</text>
  </g>
</svg>
<h2 class="abs heading" style="left:0;width:1200px;top:1938px;color:var(--white)">Our <b style="color:#c8283f;font-weight:500">Services</b></h2>

<!-- news -->
<h2 class="abs heading" style="left:0;width:1200px;top:2885px">IT <b>News</b></h2>
<div class="news-card" style="left:90px">
  <div class="news-photo" role="img" aria-label="Photo of a person working in a server room" style="background:linear-gradient(135deg,#1d2a3c,#5c6f88,#1a2230)"></div>
  <div class="news-date">▦ Oct 27 2018</div>
  <div class="news-title">Sed ut perspiciatis unde omnis iste</div>
  <p class="news-text">Sed ut perspiciatis unde omnis iste natus error sit voluptatem accusantium doloremque laudantium, totam rem aperiam</p>
  <div class="news-more">Read More</div>
</div>
<div class="news-card" style="left:435px">
  <div class="news-photo" role="img" aria-label="Photo of two engineers with a laptop among server racks" style="background:linear-gradient(135deg,#20262e,#6d7683,#1b1f26)"></div>
  <div class="news-date">▦ Oct 27 2018</div>
  <div class="news-title">Sed ut perspiciatis unde omnis iste</div>
  <p class="news-text">Sed ut perspiciatis unde omnis iste natus error sit voluptatem accusantium doloremque laudantium, totam rem aperiam</p>
  <div class="news-more">Read More</div>
</div>
<div class="news-card" style="left:784px">
  <div class="news-photo" role="img" aria-label="Photo of a technician in a bright data center" style="background:linear-gradient(135deg,#3b4552,#a9b3bd,#4a5360)"></div>
  <div class="news-date">▦ Oct 27 2018</div>
  <div class="news-title">Sed ut perspiciatis unde omnis iste</div>
  <p class="news-text">Sed ut perspiciatis unde omnis iste natus error sit voluptatem accusantium doloremque laudantium, totam rem aperiam</p>
  <div class="news-more">Read More</div>
</div>

<!-- contact -->
<h2 class="abs heading" style="left:0;width:1200px;top:3372px">Contact <b>Bork Ventures, Inc</b></h2>
<div class="abs contact-sub">Contact us for more information</div>
<div class="abs contact-item" style="left:185px">
  <div class="contact-icon"><svg width="44" height="44" viewBox="0 0 44 44" fill="none" stroke="var(--white)" stroke-width="2"><path d="M22 38s-11-12-11-20a11 11 0 0122 0c0 8-11 20-11 20z"/><circle cx="22" cy="18" r="4"/><path d="M8 38h28"/></svg></div>
  <div>2210 Fenwick Lane<br>Ashcombe, MD 20900</div>
</div>
<div class="abs contact-item" style="left:474px">
  <div class="contact-icon"><svg width="46" height="46" viewBox="0 0 46 46" fill="none" stroke="var(--white)" stroke-width="2"><rect x="5" y="11" width="36" height="24"/><path d="M5 11l18 14 18-14M5 35l13-12M41 35L28 23"/></svg></div>
  <div style="margin-top:8px">Email:<br>info@borkventuresinc.example</div>
</div>
<div class="abs contact-item" style="left:740px">
  <div class="contact-icon"><svg width="40" height="40" viewBox="0 0 40 40" fill="none" stroke="var(--white)" stroke-width="2"><path d="M11 6c3-2 4-1 5 2l2 4c1 2 0 3-2 4 2 4 5 7 9 9 1-2 2-3 4-2l4 2c3 1 4 2 2 5-3 4-8 3-14-2S6 17 6 12c0-3 2-5 5-6z"/></svg></div>
  <div>Phone:<br>301-555-0187</div>
</div>

<div class="field" style="left:166px;top:3667px">👤 First Name</div>
<div class="field" style="left:614px;top:3667px">👤 Last Name</div>
<div class="field" style="left:166px;top:3721px">▯ Company</div>
<div class="field field-message" style="left:614px;top:3721px">💬 Message :</div>
<div class="field" style="left:166px;top:3775px">✉ Email Address</div>
<div class="field" style="left:166px;top:3829px">☏ Phone Number</div>
<a class="btn btn-solid" style="left:503px;top:3886px;width:205px;height:54px;font-size:17px"><svg width="18" height="18" viewBox="0 0 18 18"><path d="M1 9L17 1 13 17 9 11z" fill="var(--white)"/></svg>SUBMIT</a>

<!-- footer -->
<svg class="abs" style="left:0;top:3995px" width="1200" height="475" viewBox="0 0 1200 475" role="img" aria-label="Dark footer band with faint network pattern">
  <polygon points="0,10 333,54 600,120 867,57 1200,10 1200,475 0,475" fill="var(--footer)"/>
  <polyline points="0,10 333,54 600,120 867,57 1200,10" fill="none" stroke="var(--red)" stroke-width="3"/>
  <g fill="var(--white)" stroke="var(--red)" stroke-width="3">
    <circle cx="333" cy="54" r="11"/><circle cx="600" cy="120" r="14"/><circle cx="867" cy="57" r="11"/>
  </g>
</svg>
<div class="abs footer-brand"><span class="brand-name">Bork Ventures</span><span class="tagline-text">Insight Trust Delivery</span></div>
<div class="abs social"><span></span><span></span><span></span><span></span></div>
<div class="abs footer-nav" style="top:4333px"><span>Home</span>|<span>About Us</span>|<span>Our Services</span>|<span>Strategy</span>|<span>IT News</span>|<span>Contact Us</span></div>
<div class="abs footer-nav" style="top:4378px"><span>Privacy Policy</span>|<span>Terms of Use</span>|<span>Disclaimer</span></div>
<div class="abs footer-nav" style="top:4423px">Copyright © 2019. All Rights Reserved</div>

</body>
</html>
```